BRIGHTWAY MOTOR SALES
BRIGHTWAY MOTOR SALES -
Creative Brief
Professional
DARYL FENN
SALES REP
472 N.CORBIN AVE FAIRBROOK OHIO 45990
BRIGHTWAYMOTORSALES@EXAMPLEMAIL.COM
WWW.CRESTVALEMOTORCARS.EXAMPLE

```html
<!DOCTYPE html>
<html lang="en">
<head>
<meta charset="utf-8">
<title>Brightway Motor Sales – Business Card</title>
<link rel="stylesheet" href="https://fonts.googleapis.com/css2?family=Open+Sans:wght@400;600;700&display=swap">
<style>
  :root {
    --stage: #3a3a3c;
    --card: #ffffff;
    --magenta: #c8288f;
    --green: #7cc242;
    --ink: #4a4a4a;
    --rule: #d9d9d9;
    --art-a: #e04aa8;
    --art-b: #f7c3e3;
  }
  * { box-sizing: border-box; margin: 0; padding: 0; }
  html, body { width: 1200px; height: 780px; overflow: hidden; }
  body {
    background: var(--stage);
    font-family: "Open Sans", Arial, sans-serif;
    position: relative;
  }
  .card {
    position: absolute;
    left: 100px; top: 105px;
    width: 1000px; height: 570px;
    background: var(--card);
    border-radius: 28px;
    overflow: hidden;
  }
  .brand {
    position: absolute;
    left: 60px; top: 120px;
    width: 310px;
    text-align: center;
  }
  .brand-art {
    width: 260px; height: 150px;
    margin: 0 auto 18px;
    border-radius: 70px 90px 30px 30px;
    background: linear-gradient(160deg, var(--art-b), var(--art-a));
  }
  .brand-name {
    color: var(--magenta);
    font-weight: 700;
    font-size: 26px;
    letter-spacing: 1px;
    line-height: 1.2;
  }
  .divider {
    position: absolute;
    left: 430px; top: 70px;
    width: 2px; height: 330px;
    background: var(--rule);
  }
  .contact {
    position: absolute;
    left: 470px; top: 62px;
    right: 30px;
    color: var(--ink);
  }
  .person-name {
    color: var(--magenta);
    font-weight: 700;
    font-size: 40px;
    line-height: 1.1;
  }
  .person-role {
    color: var(--green);
    font-weight: 600;
    font-size: 24px;
    margin-bottom: 44px;
  }
  .address { font-size: 24px; line-height: 1.3; margin-bottom: 40px; }
  .line {
    display: flex; align-items: center; gap: 14px;
    font-size: 23px; line-height: 1.55;
  }
  .line svg { width: 22px; height: 22px; flex: none; }
  .stripe-green {
    position: absolute; left: 0; right: 0; bottom: 70px;
    height: 8px; background: var(--green);
  }
  .band {
    position: absolute; left: 0; right: 0; bottom: 0;
    height: 66px;
    background: var(--magenta);
    color: #fff;
    font-size: 22px;
    text-align: center;
    line-height: 66px;
    letter-spacing: 0.5px;
  }
</style>
</head>
<body>
  <div class="card">
    <div class="brand">
      <div class="brand-art" role="img" aria-label="Cartoon illustration of a small pink car"></div>
      <div class="brand-name">BRIGHTWAY<br>MOTOR SALES</div>
    </div>

    <div class="divider"></div>

    <div class="contact">
      <div class="person-name">Daryl Fenn</div>
      <div class="person-role">Sales rep</div>
      <div class="address">472 N.Corbin Ave<br>Fairbrook Ohio 45990</div>

      <div class="line">
        <svg viewBox="0 0 24 24" aria-hidden="true"><path fill="var(--magenta)" d="M6.6 10.8a15 15 0 0 0 6.6 6.6l2.2-2.2a1 1 0 0 1 1-.25 11.4 11.4 0 0 0 3.6.57 1 1 0 0 1 1 1V20a1 1 0 0 1-1 1A17 17 0 0 1 3 4a1 1 0 0 1 1-1h3.5a1 1 0 0 1 1 1c0 1.250.2 2.450.57 3.57a1 1 0 0 1-.25 1z"/></svg>
        <span>513-555-0142</span>
      </div>
      <div class="line">
        <svg viewBox="0 0 24 24" aria-hidden="true"><rect x="6" y="2" width="12" height="20" rx="2" fill="var(--magenta)"/><rect x="8" y="5" width="8" height="12" fill="#fff"/><circle cx="12" cy="19.3" r="1.1" fill="#fff"/></svg>
        <span>513-555-0187</span>
      </div>
      <div class="line">
        <svg viewBox="0 0 24 24" aria-hidden="true"><circle cx="12" cy="12" r="11" fill="var(--magenta)"/><text x="12" y="16.5" text-anchor="middle" font-size="14" font-weight="700" fill="#fff" font-family="Open Sans, sans-serif">@</text></svg>
        <span>brightwaymotorsales@examplemail.com</span>
      </div>
    </div>

    <div class="stripe-green"></div>
    <div class="band">www.crestvalemotorcars.example</div>
  </div>
</body>
</html>
```